Oven Cleaning flyer design

Hi there,
I need help designing a letterbox flyer. It needs to be DL size.
I have attached a rough design made with Chat GPT.
Would like back and front, have my business colors.
Please find attached mock up of what I would roughly like.
Also find attached logo.
Thank you

Target Market(s)

Home owners over 40

Industry/Entity Type

Cleaning

Requirements
Must have
• Logo, before after of oven, brand colors

```html
<!DOCTYPE html>
<html lang="en">
<head>
<meta charset="utf-8">
<title>Gleam Oven Care – DL Flyer Front and Back</title>
<link rel="stylesheet" href="https://fonts.googleapis.com/css2?family=Unbounded:wght@800&family=Poppins:wght@400;600;700;800&family=Roboto:wght@700;900&family=Oswald:wght@500&display=swap">
<style>
  :root{
    --teal:#45bfc8;
    --teal-deep:#3fb4bd;
    --ink:#111111;
    --paper:#ffffff;
    --stage:#545454;
  }
  *{box-sizing:border-box;margin:0;padding:0}
  html,body{width:1200px;height:1150px;overflow:hidden;background:var(--stage)}
  .flyer{position:absolute;top:80px;width:482px;height:990px;background:var(--paper);overflow:hidden;font-family:"Poppins",sans-serif}
  .flyer--front{left:95px}
  .flyer--back{left:612px}
  .flyer__bands{position:absolute;inset:0;width:100%;height:100%}
  .abs{position:absolute}
  .center{left:0;right:0;text-align:center}

  .brand{position:absolute;left:0;right:0;display:flex;align-items:center;justify-content:center;gap:14px;color:var(--teal);font-family:"Poppins",sans-serif;font-weight:800}
  .brand__dot{width:62px;height:62px;border-radius:50%;background:var(--teal)}
  .brand__name{line-height:1}
  .brand__main{display:block;font-size:40px;letter-spacing:2px}
  .brand__sub{display:block;font-size:12px;letter-spacing:6px;margin-top:6px}

  .headline{font-family:"Unbounded",sans-serif;font-weight:800;text-transform:uppercase;line-height:1}
  .headline--light{color:var(--paper);text-shadow:0 2px 8px rgba(0,0,0,.25)}
  .headline--dark{color:var(--ink)}

  .pitch{left:68px;top:326px;width:333px;height:218px;background:var(--ink);border-radius:12px;color:var(--paper);font-weight:600;font-size:18.5px;line-height:29px;text-align:center;padding-top:14px;z-index:3}
  .pitch__accent{color:var(--teal)}

  .compare{left:27px;top:507px;width:428px;height:251px;background:var(--paper);border-radius:20px;z-index:2}
  .compare__photo{position:absolute;top:6px;height:237px}
  .compare__photo--before{left:7px;width:202px;border-radius:14px 0 0 14px;background:radial-gradient(circle at 55% 35%,#d9a240 0%,#8a5a1c 45%,#2a1c10 100%)}
  .compare__photo--after{left:223px;width:200px;border-radius:0 14px 14px 0;background:linear-gradient(180deg,#1f3550 0%,#2e4a6a 55%,#c9a46a 85%,#2a2f38 100%)}
  .compare__label{top:762px;color:var(--paper);font-weight:700;font-size:22px}

  .cta-pill{left:138px;top:811px;width:206px;height:47px;border-radius:24px;background:var(--ink);color:var(--teal);font-weight:700;font-size:21px;display:flex;align-items:center;justify-content:center}
  .tagline{top:869px;color:var(--teal);font-weight:700;font-size:26.5px}
  .phone-icon{border-radius:50%;background:var(--teal);display:flex;align-items:center;justify-content:center}
  .phone-number{font-family:"Roboto",sans-serif;font-weight:900;line-height:1;letter-spacing:-1px}

  .reasons{left:46px;top:278px;width:420px;list-style:none;color:var(--paper);font-weight:600;font-size:14.3px;line-height:17.5px}
  .reasons li{position:relative;padding-left:18px;margin-bottom:16px}
  .reasons li::before{content:"";position:absolute;left:0;top:2px;width:12px;height:12px;border-radius:50%;border:2px solid var(--paper)}

  .offer__lead{top:548px;font-size:29px;font-weight:400;color:var(--ink)}
  .offer__main{top:584px;font-family:"Roboto",sans-serif;font-weight:900;font-size:42px;color:var(--ink);letter-spacing:-.5px}
  .offer__main em{font-style:normal;color:var(--teal)}

  .feature{position:absolute;top:655px;width:150px;text-align:center}
  .feature__badge{width:100px;height:100px;margin:0 auto;border-radius:50%;background:var(--ink);border:3px solid var(--teal);box-shadow:0 0 0 3px var(--ink);display:flex;align-items:center;justify-content:center}
  .feature__label{margin-top:13px;color:var(--paper);font-weight:700;font-size:19px;line-height:21px}

  .contact-box{left:25px;top:836px;width:432px;height:118px;background:var(--ink);border-radius:14px}
  .website{top:908px;color:var(--teal);font-size:29.5px;font-weight:400;line-height:1}
  .extras{top:953px;color:var(--paper);font-family:"Oswald",sans-serif;font-weight:500;font-size:19px}
</style>
</head>
<body>

<!-- FRONT -->
<section class="flyer flyer--front">
  <svg class="flyer__bands" viewBox="0 0 482 990" preserveAspectRatio="none" aria-hidden="true">
    <path d="M0 61 Q241 203 482 61 L482 786 Q241 890 0 786 Z" fill="var(--teal)"/>
  </svg>

  <div class="brand" style="top:24px">
    <span class="brand__dot"></span>
    <span class="brand__name"><span class="brand__main">GLEAM</span><span class="brand__sub">OVEN CARE</span></span>
  </div>

  <h1 class="abs center headline headline--light" style="top:167px;font-size:40px">Bring Your</h1>
  <p class="abs center headline headline--dark" style="top:213px;font-size:40px">Oven Back</p>
  <p class="abs center headline headline--light" style="top:259px;font-size:40px">To Life</p>

  <div class="abs pitch">
    Professional,<br>
    <span class="pitch__accent">Non-caustic oven cleaning</span><br>
    that removes built-up grease,<br>
    smoke,and burnt grime<br>
    leaving your<br>
    oven looking fresh again.
  </div>

  <div class="abs compare">
    <div class="compare__photo compare__photo--before" role="img" aria-label="Photo of a dirty oven interior caked in burnt grease before cleaning"></div>
    <div class="compare__photo compare__photo--after" role="img" aria-label="Photo of the same oven interior clean and shining after cleaning"></div>
  </div>
  <p class="abs compare__label" style="left:63px;width:140px;text-align:center">BEFORE</p>
  <p class="abs compare__label" style="left:267px;width:140px;text-align:center">AFTER</p>

  <div class="abs cta-pill">Call Now for</div>
  <p class="abs center tagline">FAST, PROFESSIONAL SERVICE</p>

  <div class="abs phone-icon" style="left:49px;top:912px;width:52px;height:52px">
    <svg width="26" height="26" viewBox="0 0 24 24" aria-hidden="true"><path d="M6.6 10.8a15.1 15.1 0 0 0 6.6 6.6l2.2-2.2a1 1 0 0 1 1-.25 11.4 11.4 0 0 0 3.6.57 1 1 0 0 1 1 1V20a1 1 0 0 1-1 1A17 17 0 0 1 3 4a1 1 0 0 1 1-1h3.5a1 1 0 0 1 1 1c0 1.25.2 2.45.57 3.57a1 1 0 0 1-.25 1z" fill="none" stroke="#fff" stroke-width="1.8"/></svg>
  </div>
  <p class="abs phone-number" style="left:107px;top:910px;font-size:53px;color:var(--ink)">0400 555 218</p>
</section>

<!-- BACK -->
<section class="flyer flyer--back">
  <svg class="flyer__bands" viewBox="0 0 482 990" preserveAspectRatio="none" aria-hidden="true">
    <defs>
      <linearGradient id="backBand" x1="0" y1="0" x2="1" y2="1">
        <stop offset="0" stop-color="#45bfc8"/>
        <stop offset="1" stop-color="#3aafb8"/>
      </linearGradient>
    </defs>
    <path d="M0 92 Q241 196 482 92 L482 477 Q241 587 0 477 Z" fill="url(#backBand)"/>
    <path d="M0 661 Q241 783 482 661 L482 990 L0 990 Z" fill="var(--teal)"/>
  </svg>

  <div class="brand" style="top:28px">
    <span class="brand__dot"></span>
    <span class="brand__name"><span class="brand__main">GLEAM</span><span class="brand__sub">OVEN CARE</span></span>
  </div>

  <h2 class="abs headline headline--light" style="left:33px;top:174px;font-size:39px">Why Choose</h2>
  <p class="abs headline headline--dark" style="left:33px;top:228px;font-size:26px">Gleam Oven Care?</p>

  <ul class="abs reasons">
    <li>We're a local family business providing professional</li>
    <li>Non-caustic oven cleaning across Sunshine Coast.</li>
    <li>Using specialized-equipment and proven cleaning methods.</li>
    <li>We remove heavy grease, carbon build-up, smoke residue, restoring your oven safely and effectively.</li>
  </ul>

  <p class="abs center offer__lead">Mention this flyer for</p>
  <p class="abs center offer__main"><em>$10 off</em> your first clean</p>

  <div class="feature" style="left:10px">
    <div class="feature__badge">
      <svg width="46" height="46" viewBox="0 0 24 24" aria-hidden="true"><path d="M4 12.5l5 5L20 6.5" fill="none" stroke="#fff" stroke-width="2" stroke-linecap="round" stroke-linejoin="round"/></svg>
    </div>
    <p class="feature__label">Reliable<br>Service</p>
  </div>
  <div class="feature" style="left:166px">
    <div class="feature__badge">
      <svg width="46" height="46" viewBox="0 0 24 24" aria-hidden="true"><rect x="3" y="4" width="18" height="16" rx="2" fill="none" stroke="#fff" stroke-width="1.6"/><line x1="3" y1="8" x2="21" y2="8" stroke="#fff" stroke-width="1.6"/><rect x="6" y="11" width="12" height="6" fill="none" stroke="#fff" stroke-width="1.6"/></svg>
    </div>
    <p class="feature__label" style="margin-top:17px">Non-Caustic<br>Cleaning</p>
  </div>
  <div class="feature" style="left:322px">
    <div class="feature__badge">
      <svg width="46" height="46" viewBox="0 0 24 24" aria-hidden="true"><path d="M12 3l7 3v6c0 4.5-3 7.5-7 9-4-1.5-7-4.5-7-9V6z" fill="none" stroke="#fff" stroke-width="1.6" stroke-linejoin="round"/><path d="M8.5 12l2.5 2.5 4.5-5" fill="none" stroke="#fff" stroke-width="1.6" stroke-linecap="round" stroke-linejoin="round"/></svg>
    </div>
    <p class="feature__label" style="margin-top:17px">Satisfaction<br>Guaranteed</p>
  </div>

  <div class="abs contact-box"></div>
  <div class="abs phone-icon" style="left:61px;top:846px;width:51px;height:51px">
    <svg width="26" height="26" viewBox="0 0 24 24" aria-hidden="true"><path d="M6.6 10.8a15.1 15.1 0 0 0 6.6 6.6l2.2-2.2a1 1 0 0 1 1-.25 11.4 11.4 0 0 0 3.6.57 1 1 0 0 1 1 1V20a1 1 0 0 1-1 1A17 17 0 0 1 3 4a1 1 0 0 1 1-1h3.5a1 1 0 0 1 1 1c0 1.25.2 2.45.57 3.57a1 1 0 0 1-.25 1z" fill="none" stroke="#fff" stroke-width="1.8"/></svg>
  </div>
  <p class="abs phone-number" style="left:119px;top:845px;font-size:53px;color:var(--paper)">0400 555 218</p>
  <p class="abs center website">gleamovencare.com.au</p>
  <p class="abs center extras">We also clean cooktops, rangehoods and BBQs</p>
</section>

</body>
</html>
```